Graphics Design of Physics Book

Hi
Size : 8" x 11.25"
We are education book Publication Company and would like to have book cover for "Physics" it has 4 volumes. All 4 having the same color scheme and design except the volume no.
Blue is my personal favorite but u can use any color. Want to have a band at the bottom of the cover to place our Logo “VORNA Education” a PDF of the same is attached, or you can place logo anywhere according to ur design.
I need “Physics” as title of the book to be visible prominently.
And volume and volume no. should also be Visible and eye catching I prefer a Graphic to enhance the Volume No.
A background pattern can also be a option (it should be vector form so that color can be change later)
Please do not offer any cut and paste design I need very professional presentation.
Volume and Number can be in metallic 3D (CMYK) effect.
only Professional presentation will get feedback.
I have provided a sample artwork for reference do not follow it but can be a reference what I needed !

Target Market(s)

Students Class 9th to 12th

Industry/Entity Type

Education

Font styles to use
Serif

Colors
3176b5
0555a3
85abd2
cadf82
abd036
9bcb3c

Requirements
Must have
• Eye catching.
• “Physics” as title of the book to be visible prominently.
• volume and volume no. should also be Visible and eye catching
• I prefer a Graphic to enhance the Volume No.
• Icons for
• 1. Questions and answers
• 2. Theory Notes
• 3. Tips & Tricks
• 4. Previous Year's Reference Questions
• 5. Covers Complete Syllabus
Nice to have
• decent seamless background or metallic 3d effect (not to be print in special Ink) design should only be in CMYK.
Should not have
• Physics related Pictures or Icons (Specially E=mc2) or any scientist photograph or I Need pure graphic design

```html
<!DOCTYPE html>
<html lang="en">
<head>
<meta charset="utf-8">
<title>Physics Volume 1</title>
<link href="https://fonts.googleapis.com/css2?family=Anton&family=Montserrat:wght@800&display=swap" rel="stylesheet">
<style>
  :root {
    --navy-deep: #2a2d4e;
    --navy-glow: #3a3f8c;
    --ink: #ffffff;
    --silver-light: #f2f2f2;
    --silver-mid: #b5b5b5;
    --silver-dark: #6f6f6f;
    --band-ink: #2b2b2b;
  }
  html, body { margin: 0; padding: 0; overflow: hidden; background: var(--navy-deep); }
  .cover {
    position: relative;
    width: 853px; height: 1200px; overflow: hidden;
    background: radial-gradient(ellipse 420px 420px at 432px 580px, var(--navy-glow), var(--navy-deep) 100%);
  }
  .rule {
    position: absolute; left: 0; width: 853px; height: 14px;
    background: linear-gradient(to bottom, #222 0, var(--silver-dark) 15%, var(--silver-light) 50%, var(--silver-mid) 80%, #333 100%);
    border-top: 3px solid #1e2038;
  }
  .rule--top { top: 103px; }
  .rule--bottom { top: 385px; }
  .title, .volume { position: absolute; left: 0; }
  .title { top: 140px; }
  .volume { top: 430px; }
  .features {
    position: absolute; left: 44px; top: 588px; margin: 0; padding: 0; list-style: none;
  }
  .feature {
    display: flex; align-items: center; height: 90px;
    font-family: "Anton", sans-serif; font-size: 40px; color: var(--ink); letter-spacing: 0.2px;
  }
  .feature svg { width: 76px; height: 60px; margin-right: 26px; flex: none; }
  .band {
    position: absolute; left: 0; top: 1100px; width: 853px; height: 70px;
    background: linear-gradient(to right, #9a9a9a, #f4f4f4 20%, #a8a8a8 45%, #d8d8d8 60%, #f4f4f4 80%, #9a9a9a);
    display: flex; align-items: center; justify-content: center;
  }
  .brand {
    font-family: "Montserrat", sans-serif; font-weight: 800; font-size: 30px;
    color: var(--band-ink); letter-spacing: 2px;
  }
</style>
</head>
<body>
<div class="cover">
  <svg width="0" height="0" style="position:absolute">
    <defs>
      <linearGradient id="metal" x1="0" y1="0" x2="0" y2="1">
        <stop offset="0" stop-color="#ffffff"/>
        <stop offset="0.35" stop-color="#e6e6e6"/>
        <stop offset="0.6" stop-color="#8a8a8a"/>
        <stop offset="0.85" stop-color="#3c3c3c"/>
        <stop offset="1" stop-color="#5a5a5a"/>
      </linearGradient>
      <linearGradient id="metal-small" x1="0" y1="0" x2="0" y2="1">
        <stop offset="0" stop-color="#ffffff"/>
        <stop offset="0.5" stop-color="#cfcfcf"/>
        <stop offset="0.55" stop-color="#777"/>
        <stop offset="1" stop-color="#bdbdbd"/>
      </linearGradient>
    </defs>
  </svg>

  <div class="rule rule--top"></div>

  <svg class="title" width="853" height="230" viewBox="0 0 853 230">
    <text x="426" y="212" text-anchor="middle" textLength="804" lengthAdjust="spacingAndGlyphs"
      font-family="Anton, sans-serif" font-size="250" fill="url(#metal)" stroke="#ffffff" stroke-width="2">PHYSICS</text>
  </svg>

  <div class="rule rule--bottom"></div>

  <svg class="volume" width="853" height="90" viewBox="0 0 853 90">
    <text x="426" y="68" text-anchor="middle" font-family="Montserrat, sans-serif" font-weight="800"
      font-size="64" fill="url(#metal-small)" stroke="#e0e0e0" stroke-width="0.8">Volume1</text>
  </svg>

  <ul class="features">
    <li class="feature">
      <svg viewBox="0 0 76 60" fill="none" stroke="#fff" stroke-width="3">
        <path d="M30 6a22 18 0 1 1-12 34l-10 6 4-10A22 18 0 0 1 30 6z" fill="#2f3360"/>
        <path d="M50 20a20 16 0 0 1 8 30l6 8-12-4a20 16 0 0 1-14-2" />
        <text x="30" y="31" text-anchor="middle" font-family="Montserrat, sans-serif" font-weight="800" font-size="14" fill="#fff" stroke="none">Q&amp;A</text>
      </svg>
      Questions and answers
    </li>
    <li class="feature">
      <svg viewBox="0 0 76 60" fill="none" stroke="#fff" stroke-width="3">
        <path d="M40 10H10v44h44V26"/>
        <path d="M58 4l8 8-26 26-11 3 3-11z"/>
      </svg>
      Theory Notes
    </li>
    <li class="feature">
      <svg viewBox="0 0 76 60" fill="none" stroke="#fff" stroke-width="3">
        <path d="M38 14a13 13 0 0 0-8 23v7h16v-7a13 13 0 0 0-8-23z"/>
        <path d="M31 49h14M33 54h10"/>
        <path d="M38 2v6M20 8l4 5M56 8l-4 5M12 24h6M58 24h6M16 38l5-3M60 38l-5-3" stroke-width="2.5"/>
      </svg>
      Tips &amp; Tricks
    </li>
    <li class="feature">
      <svg viewBox="0 0 76 60" fill="none" stroke="#fff" stroke-width="3.5">
        <path d="M16 42a24 24 0 1 0-2-18"/>
        <path d="M8 22l6 6 6-7"/>
        <path d="M38 16v14l-10 8"/>
      </svg>
      Previous Year's Reference Questions
    </li>
    <li class="feature">
      <svg viewBox="0 0 76 60" fill="none" stroke="#fff" stroke-width="2.5">
        <path d="M26 6h-8v50h34V6h-8"/>
        <rect x="26" y="3" width="18" height="7" rx="2"/>
        <path d="M22 20l3 3 5-5M34 21h12M22 32l3 3 5-5M34 33h12M22 44l3 3 5-5"/>
        <circle cx="52" cy="48" r="8" fill="#fff"/>
        <path d="M48 48l3 3 5-5" stroke="#2a2d4e"/>
      </svg>
      Covers Complete Syllabus
    </li>
  </ul>

  <div class="band">
    <span class="brand">VORNA Education</span>
  </div>
</div>
</body>
</html>
```